Harborview Estates Business Card for Apartment Buildings

Create business cards for resident managers who run apartment buildings. The audience is the public who are searching for apartment rentals, and current residents who live at the apartment building. Key design element will be incorporating the company logo, however, the logo cannot dominate. The building name and manager name are more important than the logo. Current business card design leaves little room for copy, so we may need to reduce the size on the current card to allow for more space for copy.

Target Market(s)

Adults 18-65 years of age, who are looking for an apartment rental, plus current residents who live at our apartment buildings.

Industry/Entity Type

Property Management

Contact Information for Business Card

A major design element will be use of the company logo. Important property and manager contact information must be part of the design. The size of the logo will need to be reduced to make room for building and manager contact copy.

Font styles to use
Sans Serif

Colors
3176b5
000000
959595
ffffff

Requirements
Must have
• 1) Incorporate the company logo.
• 2) Use the company colors (dark blue, black/grey, over white).
• 3) FEATURE THE BUILDING NAME
• 4) FEATURE THE MANAGER NAME
• 5) The company name is less important than BUILDING and MANAGER
• 6) Manager contact information
• **SEE ATTACHED CREATIVE BRIEF**
Nice to have
• 1) Back of card logo watermark
• 2) Ability to write notes on back of carfd
Should not have
• Avoid letting the company logo dominate the card, the building name and manager are more important than the company logo.

```html
<!DOCTYPE html>
<html lang="en">
<head>
<meta charset="utf-8">
<title>Harborview Estates – Resident Manager Business Card</title>
<link href="https://fonts.googleapis.com/css2?family=Roboto:wght@400;500;700&display=swap" rel="stylesheet">
<style>
  :root {
    --brand-blue: #0e6caa;
    --ink-dark: #474749;
    --ink-mid: #3a3a3c;
    --paper: #ffffff;
    --stage: #e6e7e9;
    --card-edge: #cfd0d2;
    --faint-grey: #f3f3f4;
    --faint-blue: #eef3fa;
  }
  * { box-sizing: border-box; margin: 0; padding: 0; }
  html, body { width: 1200px; height: 1200px; overflow: hidden; }
  body {
    background: var(--stage);
    font-family: "Roboto", Helvetica, Arial, sans-serif;
    position: relative;
    border: 1px solid #9a9a9a;
  }
  .card {
    position: absolute;
    left: 257px;
    width: 686px;
    height: 392px;
    background: var(--paper);
    border: 1px solid var(--card-edge);
    overflow: hidden;
  }
  .card--front { top: 177px; }
  .card--back { top: 645px; }

  /* Front */
  .company-name {
    position: absolute;
    right: 36px;
    top: 36px;
    color: var(--brand-blue);
    font-weight: 700;
    font-size: 27px;
    letter-spacing: 0.5px;
    text-transform: uppercase;
  }
  .front-decor {
    position: absolute;
    left: 22px;
    top: 118px;
    width: 228px;
    height: 228px;
    border-radius: 50%;
    background: #ececed;
  }
  .manager {
    position: absolute;
    right: 36px;
    top: 116px;
    text-align: right;
  }
  .manager-name {
    color: var(--brand-blue);
    font-size: 27px;
    font-weight: 400;
    line-height: 1.1;
  }
  .manager-title {
    color: var(--ink-mid);
    font-size: 13px;
    margin-top: 4px;
  }
  .info-band {
    position: absolute;
    left: 256px;
    right: 0;
    top: 178px;
    height: 182px;
    background: var(--brand-blue);
    color: var(--paper);
    padding: 30px 0 0 41px;
  }
  .info-band::before {
    content: "";
    position: absolute;
    top: -8px;
    left: 357px;
    border-left: 9px solid transparent;
    border-right: 9px solid transparent;
    border-bottom: 8px solid var(--brand-blue);
  }
  .building-name { font-size: 18px; font-weight: 500; }
  .building-address { font-size: 14.5px; margin-top: 2px; }
  .contacts {
    display: grid;
    grid-template-columns: 146px auto;
    margin-top: 26px;
    font-size: 13.5px;
    row-gap: 1px;
  }
  .contact { display: flex; align-items: center; gap: 7px; height: 17px; }
  .contact svg { width: 12px; height: 12px; fill: var(--paper); flex: none; }

  /* Back */
  .back-watermark {
    position: absolute;
    left: 16px;
    top: 18px;
    width: 360px;
    height: 360px;
    border-radius: 50%;
    background: radial-gradient(circle, var(--faint-blue) 0%, var(--faint-grey) 70%);
  }
  .back-web {
    position: absolute;
    left: 35px;
    top: 349px;
    font-size: 15.5px;
    color: var(--ink-mid);
    letter-spacing: 0.6px;
  }
  .back-web strong { color: var(--brand-blue); font-weight: 500; }
  .back-mark {
    position: absolute;
    right: 24px;
    top: 336px;
    display: flex;
    align-items: center;
    gap: 6px;
    color: var(--brand-blue);
    font-size: 11px;
    font-weight: 700;
    text-transform: uppercase;
  }
  .back-mark .mark-square { width: 12px; height: 12px; background: var(--brand-blue); }
</style>
</head>
<body>

<section class="card card--front">
  <div class="company-name">Harborview Estates</div>
  <div class="front-decor" role="img" aria-label="Decorative brand shape"></div>

  <div class="manager">
    <div class="manager-name">Marisol Navarro</div>
    <div class="manager-title">Resident Manager</div>
  </div>

  <div class="info-band">
    <div class="building-name">Bayside Gardens Apartments</div>
    <div class="building-address">2485 Larkspur Street, Bay City, CA 90210</div>

    <div class="contacts">
      <div class="contact">
        <svg viewBox="0 0 12 12"><path d="M1 4c0-2 2-3 5-3s5 1 5 3v1H8V4H4v1H1z M2 6h8l1 5H1z"/></svg>
        555-201-4410
      </div>
      <div class="contact">
        <svg viewBox="0 0 12 12"><path d="M1 3h10v7H1z M1.5 3.5L6 7l4.5-3.5" fill="none" stroke="#fff"/><path d="M1 3h10L6 7z"/></svg>
        marisol@harborviewest.com
      </div>
      <div class="contact">
        <svg viewBox="0 0 12 12"><path d="M3.5 1h5v10h-5z M4.5 2v7h3V2z" fill-rule="evenodd"/></svg>
        555-387-2291
      </div>
      <div class="contact"></div>
      <div class="contact">
        <svg viewBox="0 0 12 12"><path d="M3 1h5v3H3z M1 5h10v6H1z"/></svg>
        555-640-9015
      </div>
      <div class="contact">
        <svg viewBox="0 0 12 12"><circle cx="6" cy="6" r="5" fill="none" stroke="#fff" stroke-width="1.2"/><path d="M1 6h10M6 1v10" stroke="#fff" stroke-width="1"/></svg>
        www.harborviewest.com
      </div>
    </div>
  </div>
</section>

<section class="card card--back">
  <div class="back-watermark" role="img" aria-label="Faint brand watermark"></div>
  <div class="back-web">www.<strong>harborviewest</strong>.com</div>
  <div class="back-mark"><span class="mark-square"></span>Harborview Estates</div>
</section>

</body>
</html>
```